TA BRAMLEY BUSINESS CARD DESIGN PROJECT

We need to utilize our logo that was expertly created on PixelHarbor and now need to match this with a business card design.

```html
<!DOCTYPE html>
<html lang="en">
<head>
<meta charset="utf-8">
<title>TA BRAMLEY Business Card</title>
<link rel="stylesheet" href="https://fonts.googleapis.com/css2?family=Montserrat:wght@400;700&display=swap">
<style>
  :root {
    --stage: #2e2e2e;
    --card-black: #161616;
    --card-white: #ffffff;
    --brand-blue: #1456ad;
    --text-light: #f2f2f2;
    --emboss: #2a2a2a;
  }
  * { margin: 0; padding: 0; box-sizing: border-box; }
  html, body { width: 1200px; height: 689px; overflow: hidden; }
  body {
    background: var(--stage);
    font-family: "Montserrat", sans-serif;
    position: relative;
  }
  .card {
    position: absolute;
    top: 200px;
    width: 500px;
    height: 290px;
    border-radius: 18px;
    overflow: hidden;
  }
  .card-back { left: 70px; background: var(--card-black); }
  .card-front { left: 630px; background: var(--card-white); }
  .card-front .wave { position: absolute; inset: 0; }

  .brand {
    position: absolute;
    display: flex;
    align-items: center;
    gap: 12px;
    font-weight: 700;
    letter-spacing: 4px;
    white-space: nowrap;
  }
  .brand-mark { display: block; }
  .card-back .brand {
    left: 50%; top: 50%;
    transform: translate(-50%, -50%);
    font-size: 40px;
    color: var(--emboss);
  }
  .card-back .brand-mark { width: 26px; height: 26px; background: var(--emboss); }
  .card-front .brand {
    right: 34px; top: 28px;
    font-size: 28px;
    color: var(--brand-blue);
  }
  .card-front .brand-mark { width: 20px; height: 20px; background: var(--brand-blue); }

  .contact {
    position: absolute;
    left: 40px;
    top: 154px;
    color: var(--text-light);
    font-size: 11px;
    line-height: 1.3;
  }
  .identity { border-left: 7px solid var(--brand-blue); padding-left: 10px; margin-left: -17px; }
  .person-name { color: var(--brand-blue); font-weight: 700; font-size: 17px; letter-spacing: 0.5px; line-height: 1.1; }
  .person-role { font-size: 12px; }
  .address { margin-top: 7px; }
  .lines { margin-top: 7px; list-style: none; }
  .lines li { display: flex; align-items: center; gap: 7px; }
  .lines svg { width: 10px; height: 10px; fill: var(--brand-blue); flex: none; }
</style>
</head>
<body>
  <section class="card card-back" aria-label="Card back">
    <div class="brand"><span class="brand-mark"></span>TA BRAMLEY</div>
  </section>

  <section class="card card-front" aria-label="Card front">
    <svg class="wave" viewBox="0 0 500 290" preserveAspectRatio="none" aria-hidden="true">
      <path d="M0,130 C110,80 220,112 300,112 C400,112 470,96 500,70 L500,84 C470,110 400,126 300,126 C220,126 110,96 0,152 Z" fill="var(--brand-blue)"/>
      <path d="M0,160 C110,104 220,132 300,132 C400,132 470,116 500,92 L500,290 L0,290 Z" fill="var(--card-black)"/>
    </svg>

    <div class="brand"><span class="brand-mark"></span>TA BRAMLEY</div>

    <div class="contact">
      <div class="identity">
        <p class="person-name">OWEN HARTLEY</p>
        <p class="person-role">Managing Director</p>
      </div>
      <p class="address">Your address, City<br>State, Zip 1234</p>
      <ul class="lines">
        <li><svg viewBox="0 0 10 10"><path d="M2 0h2l1 3-1.5 1a6 6 0 0 0 2.5 2.5L7 5l3 1v2a2 2 0 0 1-2 2A8 8 0 0 1 0 2a2 2 0 0 1 2-2z"/></svg>123 456 789</li>
        <li><svg viewBox="0 0 10 10"><path d="M0 2h10v6H0z M0 2l5 3.5L10 2"/></svg>info@yourgmail.com</li>
        <li><svg viewBox="0 0 10 10"><circle cx="5" cy="5" r="5"/></svg>www.yourwebsite.com</li>
      </ul>
    </div>
  </section>
</body>
</html>
```